Car wash line needed for the pylon inscription

We need a design template / print template for our advertising pylon so that the Korvane plates can be printed. The area to be printed is approx. 1.5m wide and approx. 2.70m high. We operate a car wash about 30m long. The washing rollers are equipped with scratch-free Velmo Tex foam material. Before the vehicle is put into the car wash it gets a manual high pressure pre-wash. There are four different washing programs: basic laundry € 7.50 (wheel cleaning, intensive washing, gloss drying comfort care € 10.50 (like base + active foam) special care € 13.00 (like comfort + glossy sealing with lotus wax) premium care € 15.50 (like special care + Underbody wash) The pylon is right on the driveway on a busy road, we want to achieve maximum attention with the pylons. It should not be too much content because the vehicles drive past it, due to an immediate gyro, the speed is however at about 40Km / h. Opening hours Mon-Fri. 08: 00-19: 00 Sat 07: 00-19: 00 The Korvane plates are red. The enclosed files show our pylon with a little appealing design proposal our advertising agency and the real local places. For the opinion you can see on the following link a youtube video with a comparable car wash like ours, the washing process is well illustrated there. https://www.clipvault-demo.net/watch?v=Qk7rTzP2mLw Furthermore, we have a bonus card system who has washed our car 10 times gets the 11 laundry for free. From foam additives we use active foam from the comfort care and from the special care gets the vehicle lotus wax, which has the effect that the paint is sealed and keeps the shine longer. We need a design template / print template for our advertising pylon so that the Korvane plates can be printed. The area to be printed is approx. 1.5m wide and approx. 2.70m high. We operate a car wash about 30m long. The washing rollers are equipped with scratch-free Velmo Tex foam material. Before the vehicle is put into the car wash it gets a manual high pressure pre-wash. There are four different washing programs: basic laundry € 7.50 (wheel cleaning, intensive washing, gloss drying comfort care € 10.50 (like base + active foam) special care € 13.00 (like comfort + glossy sealing with lotus wax) premium care € 15.50 (like special care + Underbody wash) The pylon is right on the driveway on a busy road, we want to achieve maximum attention with the pylons. It should not be too much content because the vehicles drive past it, due to an immediate gyro, the speed is however at about 40Km / h. Opening hours Mon-Fri. 08: 00-19: 00 Sat 07: 00-19: 00 The Korvane plates are red. The enclosed files show our pylon with a little appealing design proposal our advertising agency and the real local places. For the opinion you can see on the following link a youtube video with a comparable car wash like ours, the washing process is well illustrated there. https://www.clipvault-demo.net/watch?v=Qk7rTzP2mLw Furthermore, we have a bonus card system who has washed our car 10 times gets the 11 laundry for free. From foam additives we use active foam from the comfort care and from the special care gets the vehicle lotus wax, which has the effect that the paint is sealed and keeps the shine longer. We need a design template / print template for our advertising pylon so that the Korvane plates can be printed. The area to be printed is approx. 1.5m wide and approx. 2.70m high. We operate a car wash about 30m long. The washing rollers are equipped with scratch-free Velmo Tex foam material. Before the vehicle is put into the car wash it gets a manual high pressure pre-wash. There are four different washing programs: basic laundry € 7.50 (wheel cleaning, intensive washing, gloss drying comfort care € 10.50 (like base + active foam) special care € 13.00 (like comfort + glossy sealing with lotus wax) premium care € 15.50 (like special care + Underbody wash) The pylon is right on the driveway on a busy road, we want to achieve maximum attention with the pylons. It should not be too much content because the vehicles drive past it, due to an immediate gyro, the speed is however at about 40Km / h. Opening hours Mon-Fri. 08: 00-19: 00 Sat 07: 00-19: 00 The Korvane plates are red. The enclosed files show our pylon with a little appealing design proposal our advertising agency and the real local places. For the opinion you can see on the following link a youtube video with a comparable car wash like ours, the washing process is well illustrated there. https://www.clipvault-demo.net/watch?v=Qk7rTzP2mLw Furthermore, we have a bonus card system who has washed our car 10 times gets the 11 laundry for free. From foam additives we use active foam from the comfort care and from the special care gets the vehicle lotus wax, which has the effect that the paint is sealed and keeps the shine longer. We need a design template / print template for our advertising pylon so that the Korvane plates can be printed. The area to be printed is approx. 1.5m wide and approx. 2.70m high. We operate a car wash about 30m long. The washing rollers are equipped with scratch-free Velmo Tex foam material. Before the vehicle is put into the car wash it gets a manual high pressure pre-wash. There are four different washing programs: basic laundry € 7.50 (wheel cleaning, intensive washing, gloss drying comfort care € 10.50 (like base + active foam) special care € 13.00 (like comfort + glossy sealing with lotus wax) premium care € 15.50 (like special care + Underbody wash) The pylon is right on the driveway on a busy road, we want to achieve maximum attention with the pylons. It should not be too much content because the vehicles drive past it, due to an immediate gyro, the speed is however at about 40Km / h. Opening hours Mon-Fri. 08: 00-19: 00 Sat 07: 00-19: 00 The Korvane plates are red. The enclosed files show our pylon with a little appealing design proposal our advertising agency and the real local places. For the opinion you can see on the following link a youtube video with a comparable car wash like ours, the washing process is well illustrated there. https://www.clipvault-demo.net/watch?v=Qk7rTzP2mLw Furthermore, we have a bonus card system who has washed our car 10 times gets the 11 laundry for free. From foam additives we use active foam from the comfort care and from the special care gets the vehicle lotus wax, which has the effect that the paint is sealed and keeps the shine longer. We need a design template / print template for our advertising pylon so that the Korvane plates can be printed. The area to be printed is approx. 1.5m wide and approx. 2.70m high. We operate a car wash about 30m long. The washing rollers are equipped with scratch-free Velmo Tex foam material. Before the vehicle is put into the car wash it gets a manual high pressure pre-wash. There are four different washing programs: basic laundry € 7.50 (wheel cleaning, intensive washing, gloss drying comfort care € 10.50 (like base + active foam) special care € 13.00 (like comfort + glossy sealing with lotus wax) premium care € 15.50 (like special care + Underbody wash) The pylon is right on the driveway on a busy road, we want to achieve maximum attention with the pylons. It should not be too much content because the vehicles drive past it, due to an immediate gyro, the speed is however at about 40Km / h. Opening hours Mon-Fri. 08: 00-19: 00 Sat 07: 00-19: 00 The Korvane plates are red. The enclosed files show our pylon with a little appealing design proposal our advertising agency and the real local places. For the opinion you can see on the following link a youtube video with a comparable car wash like ours, the washing process is well illustrated there. https://www.clipvault-demo.net/watch?v=Qk7rTzP2mLw Furthermore, we have a bonus card system who has washed our car 10 times gets the 11 laundry for free. From foam additives we use active foam from the comfort care and from the special care gets the vehicle lotus wax, which has the effect that the paint is sealed and keeps the shine longer. We need a design template / print template for our advertising pylon so that the Korvane plates can be printed. The area to be printed is approx. 1.5m wide and approx. 2.70m high. We operate a car wash about 30m long. The washing rollers are equipped with scratch-free Velmo Tex foam material. Before the vehicle is put into the car wash it gets a manual high pressure pre-wash. There are four different washing programs: basic laundry € 7.50 (wheel cleaning, intensive washing, gloss drying comfort care € 10.50 (like base + active foam) special care € 13.00 (like comfort + glossy sealing with lotus wax) premium care € 15.50 (like special care + Underbody wash) The pylon is right on the driveway on a busy road, we want to achieve maximum attention with the pylons. It should not be too much content because the vehicles drive past it, due to an immediate gyro, the speed is however at about 40Km / h. Opening hours Mon-Fri. 08: 00-19: 00 Sat 07: 00-19: 00 The Korvane plates are red. The enclosed files show our pylon with a little appealing design proposal our advertising agency and the real local places. For the opinion you can see on the following link a youtube video with a comparable car wash like ours, the washing process is well illustrated there. https://www.clipvault-demo.net/watch?v=Qk7rTzP2mLw Furthermore, we have a bonus card system who has washed our car 10 times gets the 11 laundry for free. From foam additives we use active foam from the comfort care and from the special care gets the vehicle lotus wax, which has the effect that the paint is sealed and keeps the shine longer. We need a design template / print template for our advertising pylon so that the Korvane plates can be printed. The area to be printed is approx. 1.5m wide and approx. 2.70m high. We operate a car wash about 30m long. The washing rollers are equipped with scratch-free Velmo Tex foam material. Before the vehicle is put into the car wash it gets a manual high pressure pre-wash. There are four different washing programs: basic laundry € 7.50 (wheel cleaning, intensive washing, gloss drying comfort care € 10.50 (like base + active foam) special care € 13.00 (like comfort + glossy sealing with lotus wax) premium care € 15.50 (like special care + Underbody wash) The pylon is right on the driveway on a busy road, we want to achieve maximum attention with the pylons. It should not be too much content because the vehicles drive past it, due to an immediate gyro, the speed is however at about 40Km / h. Opening hours Mon-Fri. 08: 00-19: 00 Sat 07: 00-19: 00 The Korvane plates are red. The enclosed files show our pylon with a little appealing design proposal our advertising agency and the real local places. For the opinion you can see on the following link a youtube video with a comparable car wash like ours, the washing process is well illustrated there. https://www.clipvault-demo.net/watch?v=Qk7rTzP2mLw Furthermore, we have a bonus card system who has washed our car 10 times gets the 11 laundry for free. From foam additives we use active foam from the comfort care and from the special care gets the vehicle lotus wax, which has the effect that the paint is sealed and keeps the shine longer. We need a design template / print template for our advertising pylon so that the Korvane plates can be printed. The area to be printed is approx. 1.5m wide and approx. 2.70m high. We operate a car wash about 30m long. The washing rollers are equipped with scratch-free Velmo Tex foam material. Before the vehicle is put into the car wash it gets a manual high pressure pre-wash. There are four different washing programs: basic laundry € 7.50 (wheel cleaning, intensive washing, gloss drying comfort care € 10.50 (like base + active foam) special care € 13.00 (like comfort + glossy sealing with lotus wax) premium care € 15.50 (like special care + Underbody wash) The pylon is right on the driveway on a busy road, we want to achieve maximum attention with the pylons. It should not be too much content because the vehicles drive past it, due to an immediate gyro, the speed is however at about 40Km / h. Opening hours Mon-Fri. 08: 00-19: 00 Sat 07: 00-19: 00 The Korvane plates are red. The enclosed files show our pylon with a little appealing design proposal our advertising agency and the real local places. For the opinion you can see on the following link a youtube video with a comparable car wash like ours, the washing process is well illustrated there. https://www.clipvault-demo.net/watch?v=Qk7rTzP2mLw Furthermore, we have a bonus card system who has washed our car 10 times gets the 11 laundry for free. From foam additives we use active foam from the comfort care and from the special care gets the vehicle lotus wax, which has the effect that the paint is sealed and keeps the shine longer. We need a design template / print template for our advertising pylon so that the Korvane plates can be printed. The area to be printed is approx. 1.5m wide and approx. 2.70m high. We operate a car wash about 30m long. The washing rollers are equipped with scratch-free Velmo Tex foam material. Before the vehicle is put into the car wash it gets a manual high pressure pre-wash. There are four different washing programs: basic laundry € 7.50 (wheel cleaning, intensive washing, gloss drying comfort care € 10.50 (like base + active foam) special care € 13.00 (like comfort + glossy sealing with lotus wax) premium care € 15.50 (like special care + Underbody wash) The pylon is right on the driveway on a busy road, we want to achieve maximum attention with the pylons. It should not be too much content because the vehicles drive past it, due to an immediate gyro, the speed is however at about 40Km / h. Opening hours Mon-Fri. 08: 00-19: 00 Sat 07: 00-19: 00 The Korvane plates are red. The enclosed files show our pylon with a little appealing design proposal our advertising agency and the real local places. For the opinion you can see on the following link a youtube video with a comparable car wash like ours, the washing process is well illustrated there. https://www.clipvault-demo.net/watch?v=Qk7rTzP2mLw Furthermore, we have a bonus card system who has washed our car 10 times gets the 11 laundry for free. From foam additives we use active foam from the comfort care and from the special care gets the vehicle lotus wax, which has the effect that the paint is sealed and keeps the shine longer.

Target Market(s)

germany

Colors

Designer to choose colors to be used in the design.

Requirements
Must have
• Print template for the print job in the accepted formats. Of course, the design must be in German
Nice to have
• Colors that attract attention, but are still serious. The content must be perceived when passing by and the customers must be aware of the car wash.
Should not have
• Kitschiges Design Too much content which takes longer to be read.

```html
<!DOCTYPE html>
<html lang="de">
<head>
<meta charset="utf-8">
<title>Waschpark Lindenhof – Pylon</title>
<link rel="stylesheet" href="https://fonts.googleapis.com/css2?family=Archivo+Black&family=Roboto+Condensed:wght@700&display=swap">
<style>
  :root {
    --red: #c52d33;
    --frame: #30333b;
    --navy: #0b1f5a;
    --desc-blue: #0a78c6;
    --label-yellow: #ffe100;
    --label-red: #e3121c;
    --price-green: #008a3f;
    --price-red: #e81c24;
    --price-purple: #8b1868;
    --price-blue: #0e3f8f;
    --white: #ffffff;
    --hours-yellow: #ffe600;
  }
  html, body {
    margin: 0;
    padding: 0;
    width: 780px;
    height: 1200px;
    overflow: hidden;
    background: var(--white);
  }
  .pylon { display: block; width: 780px; height: 1200px; }
  .brand-dot { fill: var(--red); }
  .brand-name { font-family: "Archivo Black", "Arial Black", sans-serif; fill: var(--navy); font-size: 56px; }
  .frame { fill: var(--frame); }
  .header-bg, .hours-bg { fill: var(--navy); }
  .desc-bg { fill: var(--desc-blue); }
  .label-bg { fill: var(--label-yellow); }
  .label-divider { fill: #111; }
  .price-basis { fill: var(--price-green); }
  .price-komfort { fill: var(--price-red); }
  .price-spezial { fill: var(--price-purple); }
  .price-premium { fill: var(--price-blue); }
  .claim { font-family: "Archivo Black", "Arial Black", sans-serif; fill: var(--white); }
  .label { font-family: "Archivo Black", "Arial Black", sans-serif; fill: var(--label-red); font-size: 21px; }
  .price { font-family: "Roboto Condensed", "Arial Narrow", sans-serif; font-weight: 700; fill: var(--white); font-size: 44px; }
  .desc { font-family: "Archivo Black", "Arial Black", sans-serif; fill: var(--white); font-size: 11.5px; }
  .hours { font-family: "Roboto Condensed", "Arial Narrow", sans-serif; font-weight: 700; fill: var(--hours-yellow); font-size: 16px; }
  .hours-small { font-size: 11px; }
</style>
</head>
<body>
<svg class="pylon" viewBox="0 0 780 1200" xmlns="http://www.w3.org/2000/svg">
  <!-- business name -->
  <g class="brand">
    <circle class="brand-dot" cx="178" cy="320" r="46"/>
    <text class="brand-name" x="246" y="305" textLength="380" lengthAdjust="spacingAndGlyphs">WASCHPARK</text>
    <text class="brand-name" x="246" y="370" textLength="380" lengthAdjust="spacingAndGlyphs">LINDENHOF</text>
  </g>

  <!-- legs and cabinet -->
  <rect class="frame" x="275" y="1050" width="37" height="54"/>
  <rect class="frame" x="484" y="1050" width="37" height="54"/>
  <rect class="frame" x="231" y="483" width="344" height="573"/>

  <!-- price board -->
  <g class="price-board">
    <rect class="header-bg" x="247" y="486" width="313" height="76"/>
    <text class="claim" x="404" y="508" text-anchor="middle" font-size="15" textLength="208" lengthAdjust="spacingAndGlyphs">LACKSCHONEND DANK</text>
    <text class="claim" x="404" y="534" text-anchor="middle" font-size="27" textLength="196" lengthAdjust="spacingAndGlyphs">VELMO-TEX</text>
    <text class="claim" x="404" y="558" text-anchor="middle" font-size="27" textLength="276" lengthAdjust="spacingAndGlyphs">SCHAUMWALZEN</text>

    <rect class="hours-bg" x="247" y="990" width="313" height="60"/>
    <rect class="desc-bg" x="247" y="562" width="313" height="438"/>
    <path class="desc-bg" d="M247 999 Q404 1030 560 999 Z"/>

    <!-- Basis -->
    <polygon class="label-bg" points="247,566 414,566 403,615 247,615"/>
    <polygon class="label-divider" points="414,566 418,566 407,615 403,615"/>
    <polygon class="price-basis" points="418,566 560,566 560,615 408,615"/>
    <text class="label" x="397" y="589" text-anchor="end">BASIS</text>
    <text class="label" x="397" y="611" text-anchor="end">WÄSCHE</text>
    <text class="price" x="423" y="605">€ 7,50</text>
    <text class="desc" x="259" y="635">HD-VORWÄSCHE, FELGENREINIGUNG,</text>
    <text class="desc" x="259" y="651">INTENSIVWÄSCHE, GLANZTROCKNUNG</text>

    <!-- Komfort -->
    <polygon class="label-bg" points="247,659 414,659 403,708 247,708"/>
    <polygon class="label-divider" points="414,659 418,659 407,708 403,708"/>
    <polygon class="price-komfort" points="418,659 560,659 560,708 408,708"/>
    <text class="label" x="397" y="682" text-anchor="end">KOMFORT</text>
    <text class="label" x="397" y="704" text-anchor="end">PFLEGE</text>
    <text class="price" x="423" y="698">€ 10,50</text>
    <text class="desc" x="260" y="728">HD-VORWÄSCHE, AKTIVSCHAUM,</text>
    <text class="desc" x="260" y="743">FELGENREINIGUNG, INTENSIVWÄSCHE,</text>
    <text class="desc" x="260" y="757">GLANZTROCKNUNG</text>

    <!-- Spezial -->
    <polygon class="label-bg" points="247,766 414,766 403,815 247,815"/>
    <polygon class="label-divider" points="414,766 418,766 407,815 403,815"/>
    <polygon class="price-spezial" points="418,766 560,766 560,815 408,815"/>
    <text class="label" x="397" y="789" text-anchor="end">SPEZIAL</text>
    <text class="label" x="397" y="811" text-anchor="end">PFLEGE</text>
    <text class="price" x="423" y="805">€ 13,00</text>
    <text class="desc" x="260" y="832">HD-VORWÄSCHE, AKTIVSCHAUM,</text>
    <text class="desc" x="260" y="847">FELGENREINIGUNG, INTENSIVWÄSCHE,</text>
    <text class="desc" x="260" y="861">GLANZTROCKNUNG,</text>
    <text class="desc" x="260" y="876">HOCHGLANZVERSIEGLUNG MIT</text>
    <text class="desc" x="260" y="890">LOTUSWACHS</text>

    <!-- Premium -->
    <polygon class="label-bg" points="247,898 414,898 403,947 247,947"/>
    <polygon class="label-divider" points="414,898 418,898 407,947 403,947"/>
    <polygon class="price-premium" points="418,898 560,898 560,947 408,947"/>
    <text class="label" x="397" y="921" text-anchor="end">PREMIUM</text>
    <text class="label" x="397" y="943" text-anchor="end">PFLEGE</text>
    <text class="price" x="423" y="937">€ 15,50</text>
    <text class="desc" x="258" y="964">HD-VORWÄSCHE, AKTIVSCHAUM,</text>
    <text class="desc" x="258" y="979">FELGENREINIGUNG, UNTERBODENWÄSCHE,</text>
    <text class="desc" x="258" y="993">INTENSIVWÄSCHE, GLANZTROCKNUNG,</text>
    <text class="desc" x="258" y="1007" textLength="293" lengthAdjust="spacingAndGlyphs">HOCHGLANZVERSIEGLUNG MIT LOTUSWACHS</text>

    <text class="hours" x="253" y="1044" textLength="300" lengthAdjust="spacingAndGlyphs"><tspan class="hours-small">ÖFFNUNGSZEITEN</tspan> MO-FR.: 08:00-19:00 / SA.: 07:00-19:00</text>
  </g>
</svg>
</body>
</html>
```